business card for a massage therapy practice named 'Cedar and Willow Massage Studio'

I really need a trendy, yet easy on the eyes business card to complement my logo. Ideally with some gold or rose gold foil work.

My uploaded file of the logo I have in horizontal but I have a vertical version as well. Another color that is used in the website is a blush pink here and there. I'd like to see some trendy tropical leaves in the design.

```html
<!DOCTYPE html>
<html lang="en">
<head>
<meta charset="utf-8">
<title>Cedar and Willow Massage Studio – Business Card</title>
<link href="https://fonts.googleapis.com/css2?family=Open+Sans:wght@400;600&display=swap" rel="stylesheet">
<style>
  :root {
    --teal: #1dbe9c;
    --leaf: #8cdac2;
    --leaf-soft: #5fcfae;
    --ink: #111111;
    --white: #ffffff;
    --card-edge: #d2d2d2;
    --page: #ffffff;
  }
  * { margin: 0; padding: 0; box-sizing: border-box; }
  html, body {
    width: 973px;
    height: 1200px;
    overflow: hidden;
    background: var(--page);
    font-family: "Open Sans", Arial, sans-serif;
  }
  .sheet { position: relative; width: 973px; height: 1200px; }

  .card {
    position: absolute;
    left: 53px;
    width: 868px;
    height: 509px;
    overflow: hidden;
    text-align: center;
  }

  /* Front side */
  .card--front { top: 69px; background: var(--teal); }
  .foliage {
    position: absolute;
    opacity: 0.85;
  }
  .foliage--left {
    left: 0; top: 124px; width: 187px; height: 385px;
    background: radial-gradient(ellipse at 40% 60%, var(--leaf) 0%, var(--leaf-soft) 55%, rgba(29,190,156,0) 75%);
  }
  .foliage--top-right {
    right: 0; top: 0; width: 205px; height: 156px;
    background: radial-gradient(ellipse at 60% 30%, var(--leaf) 0%, var(--leaf-soft) 50%, rgba(29,190,156,0) 75%);
  }
  .foliage--bottom-right {
    right: 0; bottom: 0; width: 248px; height: 157px;
    background: radial-gradient(ellipse at 65% 75%, var(--leaf) 0%, var(--leaf-soft) 50%, rgba(29,190,156,0) 75%);
  }
  .brand {
    position: absolute;
    left: 0; right: 0;
    top: 186px;
    color: var(--white);
    font-weight: 400;
  }
  .brand__name {
    display: block;
    font-size: 46px;
    line-height: 56px;
  }
  .brand__tagline {
    display: block;
    font-size: 26px;
    line-height: 40px;
    letter-spacing: 4px;
    text-transform: uppercase;
  }
  .website {
    position: absolute;
    left: 0; right: 0;
    top: 380px;
    color: var(--white);
    font-size: 26px;
    line-height: 32px;
  }

  /* Back side */
  .card--back {
    top: 624px;
    background: var(--white);
    border: 2px solid var(--card-edge);
  }
  .therapist {
    position: absolute;
    left: 0; right: 0;
    top: 98px;
    font-size: 41px;
    line-height: 50px;
    color: var(--ink);
  }
  .therapist__accent { color: var(--teal); }
  .phone {
    position: absolute;
    left: 0; right: 0;
    top: 146px;
    font-size: 26px;
    line-height: 34px;
    color: var(--ink);
  }
  .social-mark {
    position: absolute;
    left: 50%;
    top: 324px;
    width: 28px;
    height: 28px;
    margin-left: -14px;
    border-radius: 50%;
    background: var(--teal);
  }
  .contact {
    position: absolute;
    left: 0; right: 0;
    top: 360px;
    font-size: 26px;
    line-height: 38px;
    color: var(--ink);
  }
</style>
</head>
<body>
<main class="sheet">
  <section class="card card--front">
    <div class="foliage foliage--left" role="img" aria-label="Tropical palm leaf illustration"></div>
    <div class="foliage foliage--top-right" role="img" aria-label="Tropical palm leaf illustration"></div>
    <div class="foliage foliage--bottom-right" role="img" aria-label="Tropical palm leaf illustration"></div>
    <h1 class="brand">
      <span class="brand__name">Cedar and Willow</span>
      <span class="brand__tagline">Massage Studio</span>
    </h1>
    <p class="website">www.cedarandwillow.com</p>
  </section>

  <section class="card card--back">
    <h2 class="therapist">
      <span class="therapist__accent">Marisol</span> Vega <span class="therapist__accent">LMT</span>
    </h2>
    <p class="phone">555 014 2837</p>
    <span class="social-mark" aria-hidden="true"></span>
    <p class="contact">
      @cedarandwillow<br>
      hello@cedarandwillow.com
    </p>
  </section>
</main>
</body>
</html>
```